New Business Card for Software Company

We are looking at rebranding a 10 year old company that specializes in PDF and DWF solutions for Architects and Engineers. We will attach the new company logo that we are going with so you can work with that and complimentary colors.
The sample information we would like on the business card is:
Gerald Pinfold
Vice President
4738 W. Harrowgate Lane. STE 305
PMB#417
Tarrow, AZ 85374
866-392-5074 US Toll Free
123-456-3190 Cell
gpinfold@plavorix.com
The old tag line that we had on the business cars was.
Delivering Dependable Document and Drawing Tools to Design Teams Everywhere.
If you have an idea for a better tag line we are open to that also.
Updates
We would like to thank all of the Designers for their wonderful work. We apologize that we will not have the time to provide feedback to everyone. There is just so many innovative and professional designs that you have all created making our decision even harder.
Target Market(s)
Architects and Engineers
Industry/Entity Type
Business
Look and feel

```html
<!DOCTYPE html>
<html lang="en">
<head>
<meta charset="utf-8">
<title>Plavorix Business Card</title>
<link href="https://fonts.googleapis.com/css2?family=Source+Sans+3:wght@400;600;700&display=swap" rel="stylesheet">
<style>
  :root {
    --page-bg: #e9e6e2;
    --card-white: #ffffff;
    --brand-orange: #f0661e;
    --brand-orange-light: #f7931e;
    --brand-red: #d9381f;
    --ink-grey: #5b5b5b;
    --ink-dark: #4a4a4a;
    --tagline: #fde7d6;
  }
  * { margin: 0; padding: 0; box-sizing: border-box; }
  html, body {
    width: 1200px; height: 720px; overflow: hidden;
    background: var(--page-bg);
    font-family: "Source Sans 3", Arial, sans-serif;
  }
  .canvas {
    position: relative; width: 1200px; height: 720px;
    display: flex; align-items: center; justify-content: center; gap: 50px;
  }
  .card {
    width: 525px; height: 300px; position: relative; overflow: hidden;
    box-shadow: 0 6px 18px rgba(0,0,0,0.18);
  }
  .card-front { background: var(--card-white); }
  .brand {
    position: absolute; left: 30px; top: 32px;
    display: flex; align-items: center; gap: 10px;
  }
  .brand-dot {
    width: 46px; height: 46px; border-radius: 50%;
    background: var(--brand-orange);
  }
  .brand-name {
    font-weight: 700; font-size: 44px; letter-spacing: -1px;
    color: var(--ink-dark); line-height: 1;
  }
  .person {
    position: absolute; left: 32px; top: 112px;
    font-size: 17px; color: var(--brand-orange); font-weight: 700;
  }
  .person .title { font-weight: 400; font-size: 13px; color: var(--ink-grey); }
  .contacts {
    position: absolute; left: 32px; top: 150px; list-style: none;
    font-size: 14px; color: var(--ink-dark); line-height: 24px;
  }
  .contacts li { display: flex; align-items: center; gap: 8px; }
  .contacts svg { width: 12px; height: 12px; fill: var(--brand-orange); }
  .address {
    position: absolute; left: 32px; top: 232px;
    font-size: 14px; color: var(--ink-dark); line-height: 21px;
  }
  .card-back {
    background: radial-gradient(ellipse at 50% 40%, var(--brand-orange-light) 0%, var(--brand-orange) 55%, var(--brand-red) 100%);
    display: flex; flex-direction: column; align-items: center;
  }
  .back-brand {
    margin-top: 52px; display: flex; flex-direction: column; align-items: center; gap: 10px;
  }
  .back-brand .brand-dot {
    width: 110px; height: 110px; background: var(--brand-orange-light);
  }
  .back-brand .brand-name { color: var(--card-white); font-size: 30px; }
  .tagline {
    position: absolute; bottom: 26px; left: 0; right: 0; text-align: center;
    color: var(--tagline); font-size: 17px; line-height: 22px;
  }
</style>
</head>
<body>
<main class="canvas">
  <section class="card card-front">
    <div class="brand">
      <span class="brand-dot"></span>
      <span class="brand-name">Plavorix</span>
    </div>
    <p class="person">Gerald Pinfold, <span class="title">Vice President</span></p>
    <ul class="contacts">
      <li><svg viewBox="0 0 12 12"><path d="M2.5 1 L4.5 1 L5.5 3.8 L4.2 4.8 Q5 7 7.2 7.8 L8.2 6.5 L11 7.5 L11 9.5 Q10.5 11 9 11 Q1 10 1 3 Q1 1.5 2.5 1 Z"/></svg>866-392-5074US(TF)</li>
      <li><svg viewBox="0 0 12 12"><rect x="3" y="0.5" width="6" height="11" rx="1"/><rect x="4" y="2" width="4" height="5" fill="#fff"/></svg>123-456-3190</li>
      <li><svg viewBox="0 0 12 12"><rect x="0.5" y="2.5" width="11" height="7.5" rx="1"/><path d="M1 3 L6 7 L11 3" stroke="#fff" stroke-width="1" fill="none"/></svg>gpinfold@plavorix.com</li>
    </ul>
    <p class="address">4738 W. Harrowgate Lane. STE 305<br>PMB#417, Tarrow, AZ 85374</p>
  </section>

  <section class="card card-back">
    <div class="back-brand">
      <span class="brand-dot"></span>
      <span class="brand-name">Plavorix</span>
    </div>
    <p class="tagline">Delivering Dependable Document and Drawing<br>Tools to Design Teams Everywhere</p>
  </section>
</main>
</body>
</html>
```